Wordpress Template Design using existing Logo and Colors

We are wanting a wordpress theme designing for our b2b marketing consultancy business. A comprehesive and elagant design to our current site www.plovtrix.com would be good.

Industry/Entity Type

Marketing

Font styles to use
Sans Serif

```html
<!DOCTYPE html>
<html lang="en">
<head>
<meta charset="utf-8">
<title>Plovtrix – B2B Data &amp; Marketing</title>
<link href="https://fonts.googleapis.com/css2?family=Open+Sans:wght@400;600;700;800&family=Montserrat:wght@600;700;800&display=swap" rel="stylesheet">
<style>
:root{
  --red:#e3262c;
  --ink:#2b2b2b;
  --text:#666;
  --slate:#4e5b6f;
  --light:#efefef;
  --line:#e2e2e2;
  --white:#fff;
}
*{box-sizing:border-box;margin:0;padding:0}
html,body{width:1200px;height:2224px;overflow:hidden;background:var(--white)}
body{font-family:"Open Sans",Arial,sans-serif;color:var(--text);position:relative}

.site-header{position:absolute;top:0;left:0;width:1200px;height:64px;background:var(--white);display:flex;align-items:center;justify-content:space-between;padding:0 40px 0 130px;z-index:2}
.brand{display:flex;align-items:center;gap:10px;font-family:"Montserrat",sans-serif;font-weight:800;font-size:30px;color:var(--red);letter-spacing:1px}
.brand-square{width:14px;height:14px;background:var(--red)}
.main-nav{display:flex;align-items:center;gap:6px;font-family:"Montserrat",sans-serif;font-weight:700;font-size:11px;color:var(--ink)}
.main-nav a{padding:8px 12px;color:inherit;text-decoration:none;letter-spacing:.5px}
.main-nav a.active{background:var(--red);color:var(--white)}
.nav-phone{display:flex;align-items:center;gap:6px;color:var(--red);font-size:13px;margin-left:8px}

.hero{position:absolute;top:64px;left:0;width:1200px;height:576px;background:linear-gradient(100deg,#d9dde2 0%,#f4f5f6 35%,#e6e8ea 60%,#b9bfc6 100%)}
.hero-caption{position:absolute;left:40px;top:180px;background:rgba(40,45,55,.72);color:var(--white);padding:14px 26px 14px 18px}
.hero-caption h1{font-family:"Montserrat",sans-serif;font-size:22px;font-weight:700}
.hero-caption p{font-size:13px;margin-top:4px}
.slider-dots{position:absolute;bottom:20px;left:0;width:100%;display:flex;justify-content:center;gap:9px}
.slider-dots span{width:7px;height:7px;border-radius:50%;background:rgba(255,255,255,.6)}
.slider-dots span.on{background:var(--white)}

.services{position:absolute;top:640px;left:0;width:1200px;height:560px}
.section-title{text-align:center;font-family:"Montserrat",sans-serif;font-weight:800;font-size:22px;color:var(--ink);letter-spacing:1px}
.section-title::after{content:"";display:block;width:44px;height:3px;background:var(--red);margin:12px auto 0}
.services .section-title{margin-top:72px}
.card-row{position:absolute;top:160px;left:132px;display:flex;gap:16px}
.service-card{width:222px;height:290px;background:var(--white);border:1px solid var(--line);box-shadow:0 2px 10px rgba(0,0,0,.08);text-align:center;padding:30px 18px 0}
.service-card svg{width:56px;height:56px}
.service-card h3{font-family:"Montserrat",sans-serif;font-size:13px;font-weight:800;color:var(--ink);margin:18px 0 12px;letter-spacing:.5px}
.service-card p{font-size:11.5px;line-height:1.6}
.btn{display:inline-block;background:var(--red);color:var(--white);font-family:"Montserrat",sans-serif;font-weight:700;font-size:11px;padding:8px 18px;letter-spacing:.5px}
.service-card .btn{margin-top:16px}

.welcome{position:absolute;top:1200px;left:0;width:1200px;height:330px;background:linear-gradient(180deg,#f3f3f3,#e7e8ea);text-align:center}
.welcome .section-title{margin-top:90px}
.welcome p{width:700px;margin:26px auto 0;font-size:13px;line-height:1.7}
.welcome .btn{margin-top:24px}

.brochure{position:absolute;top:1530px;left:0;width:1200px;height:270px;background:var(--slate);text-align:center;color:var(--white)}
.brochure h2{font-family:"Montserrat",sans-serif;font-weight:800;font-size:22px;margin-top:72px;letter-spacing:1px}
.brochure p{width:560px;margin:18px auto 0;font-size:12.5px;line-height:1.6;color:#dfe3ea}
.btn-outline{display:inline-block;margin-top:26px;border:2px solid var(--white);padding:11px 34px;font-family:"Montserrat",sans-serif;font-weight:700;font-size:14px;letter-spacing:1px}

.site-footer{position:absolute;top:1800px;left:0;width:1200px;height:380px}
.footer-cols{position:absolute;top:66px;left:130px;display:flex;gap:40px}
.footer-about{width:230px}
.footer-about .brand{font-size:26px}
.footer-about p{font-size:11px;line-height:1.7;margin-top:16px}
.footer-col h4{font-family:"Montserrat",sans-serif;font-size:12px;font-weight:800;color:var(--ink);margin-bottom:12px}
.footer-col ul{list-style:none;font-size:11px;line-height:1.9}
.quick-links{width:150px}
.contact-col{width:190px}
.contact-item{display:flex;gap:8px;font-size:11px;line-height:1.6;margin-bottom:12px}
.contact-item svg{width:14px;height:14px;flex:none;margin-top:2px}
.contact-item b{display:block;color:var(--ink);font-size:10.5px}
.copyright{position:absolute;top:2180px;left:0;width:1200px;height:44px;border-top:1px solid var(--line);text-align:center;font-size:11px;line-height:44px}
</style>
</head>
<body>

<header class="site-header">
  <div class="brand"><span class="brand-square"></span>PLOVTRIX</div>
  <nav class="main-nav">
    <a class="active" href="#">HOME</a>
    <a href="#">TARGET MARKETING</a>
    <a href="#">DATA MANAGEMENT</a>
    <a href="#">ABOUT</a>
    <span class="nav-phone">
      <svg width="14" height="14" viewBox="0 0 24 24"><path fill="#e3262c" d="M6.6 10.8a15 15 0 0 0 6.6 6.6l2.2-2.2c.3-.3.7-.4 1-.2 1.1.4 2.3.6 3.6.6.6 0 1 .4 1 1V20c0 .6-.4 1-1 1C10.6 21 3 13.4 3 4c0-.6.4-1 1-1h3.5c.6 0 1 .4 1 1 0 1.3.2 2.5.6 3.6.1.3 0 .7-.2 1z"/></svg>
      +1 (555) 014-2290
    </span>
  </nav>
</header>

<section class="hero" role="img" aria-label="Photo of a businesswoman presenting to colleagues around a meeting table in a bright office">
  <div class="hero-caption">
    <h1>How Solid is Your Marketing Data?</h1>
    <p>Convert unstructured data into actionable intelligence</p>
  </div>
  <div class="slider-dots"><span class="on"></span><span></span><span></span><span></span><span></span></div>
</section>

<section class="services">
  <h2 class="section-title">OUR SERVICES</h2>
  <div class="card-row">
    <article class="service-card">
      <svg viewBox="0 0 56 56"><g fill="#333"><ellipse cx="28" cy="12" rx="18" ry="6"/><path d="M10 16c0 3.3 8 6 18 6s18-2.7 18-6v9c0 3.3-8 6-18 6s-18-2.7-18-6z"/><path d="M10 29c0 3.3 8 6 18 6s18-2.7 18-6v9c0 3.3-8 6-18 6s-18-2.7-18-6z"/></g></svg>
      <h3>B2B DATABASE</h3>
      <p>Our focus on B2B data building leads to business intelligence. Our database has over 1,000,000 organisations and 3,000,000 decision makers.</p>
      <span class="btn">READ MORE</span>
    </article>
    <article class="service-card">
      <svg viewBox="0 0 56 56"><g fill="none" stroke="#333" stroke-width="4"><circle cx="26" cy="30" r="18"/><circle cx="26" cy="30" r="9"/></g><circle cx="26" cy="30" r="3" fill="#333"/><path d="M26 30L46 10" stroke="#333" stroke-width="3"/><path d="M42 6l8 0-2 6-6 0z" fill="#333"/></svg>
      <h3>TARGET MARKETING</h3>
      <p>We develop tailored marketing solutions based on your specific objectives, audience and budget to reach high returns on investment.</p>
      <span class="btn">READ MORE</span>
    </article>
    <article class="service-card">
      <svg viewBox="0 0 56 56"><path d="M10 30a18 18 0 0 1 36 0" fill="none" stroke="#333" stroke-width="4"/><rect x="6" y="28" width="10" height="16" rx="3" fill="#333"/><rect x="40" y="28" width="10" height="16" rx="3" fill="#333"/><path d="M45 44q0 8-12 8" fill="none" stroke="#333" stroke-width="3"/><circle cx="30" cy="52" r="3" fill="#333"/></svg>
      <h3>CALL CENTRE</h3>
      <p>When your business requires professional and cost-effective contact centre services, we have it covered for campaigns of any size.</p>
      <span class="btn">READ MORE</span>
    </article>
    <article class="service-card">
      <svg viewBox="0 0 56 56"><circle cx="28" cy="16" r="10" fill="#333"/><path d="M8 52c0-12 9-20 20-20s20 8 20 20z" fill="#333"/><path d="M28 32l-4 8 4 10 4-10z" fill="#fff"/></svg>
      <h3>DATA MANAGEMENT</h3>
      <p>We analyse your data and report on effective strategies for sourcing the data into a profitable resource.</p>
      <span class="btn">READ MORE</span>
    </article>
  </div>
</section>

<section class="welcome">
  <h2 class="section-title">WELCOME TO OUR SITE</h2>
  <p>We are a B2B data analytics and marketing consultancy helping businesses harness the power of accurate data to drive growth. Our experienced team combines strategy, technology and creativity to deliver measurable results across every stage of the sales funnel.</p>
  <span class="btn">READ MORE</span>
</section>

<section class="brochure">
  <h2>CORPORATE BROCHURE</h2>
  <p>Learn our leading target marketing and intelligent data management solutions to attain new customers for your entire product and services.</p>
  <span class="btn-outline">DOWNLOAD NOW</span>
</section>

<footer class="site-footer">
  <div class="footer-cols">
    <div class="footer-about">
      <div class="brand"><span class="brand-square"></span>PLOVTRIX</div>
      <p>Plovtrix is the premier source of trusted intelligence focused on identifying business opportunities and key decision makers throughout the Asia Pacific region.</p>
    </div>
    <div class="footer-col quick-links">
      <h4>QUICK LINKS</h4>
      <ul>
        <li>B2B database</li><li>Call centre</li><li>Research generation</li><li>Lead generation</li><li>Data management</li><li>Marketing automation</li><li>Data capture</li><li>Event management</li><li>Contact us</li>
      </ul>
    </div>
    <div class="footer-col contact-col">
      <h4>REACH US</h4>
      <div class="contact-item"><svg viewBox="0 0 24 24"><path fill="#e3262c" d="M12 2a7 7 0 0 0-7 7c0 5 7 13 7 13s7-8 7-13a7 7 0 0 0-7-7zm0 9.5A2.5 2.5 0 1 1 12 6a2.5 2.5 0 0 1 0 5.5z"/></svg><span>2150 Lakeview Drive, Suite 114, Fairmont CA 92001</span></div>
      <div class="contact-item"><svg viewBox="0 0 24 24"><path fill="#e3262c" d="M6.6 10.8a15 15 0 0 0 6.6 6.6l2.2-2.2c.3-.3.7-.4 1-.2 1.1.4 2.3.6 3.6.6.6 0 1 .4 1 1V20c0 .6-.4 1-1 1C10.6 21 3 13.4 3 4c0-.6.4-1 1-1h3.5c.6 0 1 .4 1 1 0 1.3.2 2.5.6 3.6.1.3 0 .7-.2 1z"/></svg><span><b>CALL US</b>+1 (555) 014-2290</span></div>
      <div class="contact-item"><svg viewBox="0 0 24 24"><path fill="#e3262c" d="M3 5h18v14H3zm2 2v.5l7 5 7-5V7z"/></svg><span><b>EMAIL US</b>contact@plovtrix.com</span></div>
    </div>
    <div class="footer-col contact-col">
      <h4>BRANCH OFFICE</h4>
      <div class="contact-item"><svg viewBox="0 0 24 24"><path fill="#e3262c" d="M12 2a7 7 0 0 0-7 7c0 5 7 13 7 13s7-8 7-13a7 7 0 0 0-7-7zm0 9.5A2.5 2.5 0 1 1 12 6a2.5 2.5 0 0 1 0 5.5z"/></svg><span>17 Port Road, #04-11 Harbour Point, Westport 048801</span></div>
      <div class="contact-item"><svg viewBox="0 0 24 24"><path fill="#e3262c" d="M6.6 10.8a15 15 0 0 0 6.6 6.6l2.2-2.2c.3-.3.7-.4 1-.2 1.1.4 2.3.6 3.6.6.6 0 1 .4 1 1V20c0 .6-.4 1-1 1C10.6 21 3 13.4 3 4c0-.6.4-1 1-1h3.5c.6 0 1 .4 1 1 0 1.3.2 2.5.6 3.6.1.3 0 .7-.2 1z"/></svg><span><b>CALL US</b>+65 5550 1234</span></div>
      <div class="contact-item"><svg viewBox="0 0 24 24"><path fill="#e3262c" d="M3 5h18v14H3zm2 2v.5l7 5 7-5V7z"/></svg><span><b>EMAIL US</b>asia@plovtrix.com</span></div>
    </div>
  </div>
</footer>

<div class="copyright">Copyright © 2020 - 2024 Plovtrix. All Rights Reserved.</div>

</body>
</html>
```